Business card design for new eCommerce site focusing on integrity and strong businsess tactics

We need a business card that will stand out and be memorable. Something with color that matches our company logo colors. Think high end version of Pactivo. There are 2 logos provided. The parent company is called Amber Ledge Partners and we are presenting a new and very exciting eCommerce site called BrightHarborTrade.example.

Target Market(s)

Our target markets are in the Activities, Food and Beverage, Health and Beauty

Industry/Entity Type

Marketing

Contact Information for Business Card

We have 4 members that need cards...I will provide all info to the winner of the design contest
Business Address is
4870 West 63rd Avenue, Suite C207
Phoenix AZ 85731

Font styles to use
Serif
Sans Serif

Colors

Designer to choose colors to be used in the design.

Requirements
Must have
• The card must be memorable...should be unique in design but must exude integrity and be playful .
• I have provided several colors or our parent company...please feel free to use which ever
Nice to have
• I will leave this up to you. Feel free to use other images of your choosing that wraps around our client.....Activities, Dining, Health, Beauty
Should not have
• just dont be boring

```html
<!DOCTYPE html>
<html lang="en">
<head>
<meta charset="utf-8">
<title>Amber Ledge Partners – Business Card</title>
<link rel="stylesheet" href="https://fonts.googleapis.com/css2?family=Arimo:wght@700&family=Tinos&display=swap">
<style>
  :root {
    --stage: #0f1128;
    --royal: #2c3779;
    --navy-deep: #1e2140;
    --navy-mid: #252a55;
    --navy-soft: #262b58;
    --paper: #ffffff;
    --ink: #1c1f45;
  }
  * { box-sizing: border-box; margin: 0; padding: 0; }
  html, body {
    width: 1200px; height: 1200px; overflow: hidden;
    background: var(--stage);
  }
  .card {
    position: absolute;
    left: 233px;
    width: 750px; height: 450px;
    overflow: hidden;
    background: var(--royal);
  }
  .card--front { top: 90px; }
  .card--back { top: 642px; }
  .card__shapes { position: absolute; inset: 0; width: 750px; height: 450px; }
  .brand-name {
    position: absolute;
    font-family: "Arimo", Arial, sans-serif;
    font-weight: 700;
    text-align: center;
    line-height: 1.02;
    letter-spacing: -0.5px;
  }
  .brand-seal {
    position: absolute;
    border-radius: 50%;
  }
  .card--front .brand-seal {
    left: 104px; top: 94px; width: 188px; height: 188px;
    background: var(--ink);
    box-shadow: 0 0 0 3px var(--paper), 0 0 0 4.5px var(--ink);
  }
  .card--front .brand-name--light {
    left: 20px; width: 356px; top: 298px;
    font-size: 40px; color: var(--ink);
  }
  .card--front .brand-name--dark {
    left: 420px; width: 250px; top: 110px;
    font-size: 30px; color: var(--paper);
  }
  .address {
    position: absolute;
    left: 430px; width: 240px; top: 250px;
    text-align: center;
    color: var(--paper);
    font-family: "Tinos", "Times New Roman", serif;
    font-size: 17px; line-height: 23px;
  }
  .address__icon { display: block; margin: 0 auto 6px; width: 34px; height: 34px; }
  .card--back .brand-seal {
    left: 329px; top: 80px; width: 80px; height: 80px;
    border: 5px solid var(--paper);
  }
  .card--back .brand-name {
    left: 150px; width: 440px; top: 200px;
    font-size: 46px; color: var(--paper);
  }
</style>
</head>
<body>
  <section class="card card--front" aria-label="Card front">
    <svg class="card__shapes" viewBox="0 0 750 450" aria-hidden="true">
      <polygon points="233,0 308,0 429,450 286,450 369,310" fill="var(--navy-deep)"/>
      <polygon points="308,0 359,0 429,450" fill="var(--navy-mid)"/>
      <polygon points="369,310 429,450 286,450" fill="var(--navy-soft)"/>
      <polygon points="0,0 233,0 369,310 286,450 0,450" fill="var(--paper)"/>
    </svg>
    <div class="brand-seal" aria-hidden="true"></div>
    <p class="brand-name brand-name--light">Amber Ledge<br>Partners</p>
    <p class="brand-name brand-name--dark">Amber Ledge<br>Partners</p>
    <address class="address">
      <svg class="address__icon" viewBox="0 0 34 34" aria-hidden="true">
        <circle cx="17" cy="17" r="15" fill="none" stroke="var(--paper)" stroke-width="2.5"/>
        <path d="M8.5 17.5 L17 9.5 L25.5 17.5" fill="none" stroke="var(--paper)" stroke-width="2.6" stroke-linejoin="round"/>
        <path d="M11.5 16.5 V24 H22.5 V16.5 L17 11.5 Z" fill="var(--paper)"/>
        <rect x="15.2" y="19" width="3.6" height="5" fill="var(--royal)"/>
      </svg>
      4870 West 63rd Avenue,<br>Suite C207 Phoenix AZ 85731
    </address>
  </section>

  <section class="card card--back" aria-label="Card back">
    <svg class="card__shapes" viewBox="0 0 750 450" aria-hidden="true">
      <polygon points="674,0 750,0 615,309 703,450 553,450" fill="var(--navy-deep)"/>
      <polygon points="623,0 674,0 553,450" fill="var(--navy-mid)"/>
      <polygon points="615,309 703,450 553,450" fill="var(--navy-soft)"/>
      <polygon points="750,0 615,309 703,450 750,450" fill="var(--paper)"/>
    </svg>
    <div class="brand-seal" aria-hidden="true"></div>
    <p class="brand-name">Amber Ledge Partners</p>
  </section>
</body>
</html>
```